Business Card and Simple Logo Desgin

New Zealand based start up company "Vesta Advisory LTD" requires business cards and simple logo design.

Card Content.

Vesta Advisory LTD

Rebecca Thornbury
CA, BMS (Hons)

r.thornbury@vestaadvisory.co.nz
PH +64 21 574 613

Target Market(s)

Corporate Business in IT, Finance and accounting.

Industry/Entity Type

Business

```html
<!DOCTYPE html>
<html lang="en">
<head>
<meta charset="utf-8">
<title>Vesta Advisory LTD — Business Card</title>
<link rel="stylesheet" href="https://fonts.googleapis.com/css2?family=Source+Sans+3:wght@400;600&display=swap">
<style>
  :root {
    --backdrop: #1c1c1e;
    --card-dark: #161618;
    --card-mid: #3a3a3e;
    --back-dark: #0f1416;
    --back-mid: #2b3538;
    --silver-light: #f2f2f2;
    --silver-mid: #b9b9bc;
    --silver-dark: #7d7d80;
    --copper: #c98a4e;
    --text-main: #f4f4f4;
    --text-soft: #c9c9cc;
    --brand-gold: #d9a94a;
  }
  * { box-sizing: border-box; margin: 0; padding: 0; }
  html, body {
    width: 1200px; height: 900px; overflow: hidden;
    background: var(--backdrop);
    font-family: "Source Sans 3", "Myriad Pro", sans-serif;
  }
  .canvas {
    width: 1200px; height: 900px;
    display: flex; flex-direction: column; align-items: center; justify-content: center;
    gap: 60px;
  }
  .card {
    position: relative;
    width: 560px; height: 320px;
    border-radius: 14px;
    overflow: hidden;
    box-shadow: 0 10px 30px rgba(0,0,0,.55);
  }
  .card--front {
    background: radial-gradient(ellipse at 60% 40%, var(--card-mid) 0%, var(--card-dark) 75%);
  }
  .card--back {
    background: linear-gradient(160deg, var(--back-mid) 0%, var(--back-dark) 70%);
  }
  .silver-band {
    position: absolute;
    background: linear-gradient(90deg, var(--silver-dark) 0%, var(--silver-light) 30%, var(--silver-mid) 55%, var(--silver-light) 80%, var(--silver-dark) 100%);
    border-radius: 1px;
  }
  .silver-band--top { left: 55px; right: 30px; top: 40px; height: 10px; }
  .silver-band--contact { left: 292px; right: 30px; top: 238px; height: 8px; }
  .silver-band--bottom { left: 28px; right: 30px; top: 280px; height: 11px; }

  .brand {
    position: absolute;
    display: flex; flex-direction: column; align-items: center; gap: 14px;
  }
  .card--front .brand { left: 40px; top: 88px; width: 220px; }
  .card--back .brand { left: 0; right: 0; top: 92px; }
  .brand-dot {
    width: 86px; height: 86px; border-radius: 50%;
    background: var(--copper);
  }
  .card--back .brand-dot { width: 96px; height: 96px; }
  .brand-name {
    font-weight: 600; font-size: 19px; color: var(--brand-gold);
    letter-spacing: .2px; white-space: nowrap;
  }

  .person {
    position: absolute; left: 300px; top: 96px;
  }
  .person-name { font-size: 22px; font-weight: 400; color: var(--text-main); line-height: 1.1; }
  .person-credentials { font-size: 15px; color: var(--text-soft); margin-top: 6px; padding-left: 10px; }

  .contact {
    position: absolute; left: 312px; top: 178px;
    font-size: 13px; color: var(--text-main); line-height: 1.6;
  }
</style>
</head>
<body>
<main class="canvas">
  <section class="card card--front" aria-label="Business card front">
    <div class="silver-band silver-band--top"></div>
    <div class="brand">
      <div class="brand-dot"></div>
      <div class="brand-name">Vesta Advisory LTD</div>
    </div>
    <div class="person">
      <p class="person-name">Rebecca Thornbury</p>
      <p class="person-credentials">CA, BMS (Hons)</p>
    </div>
    <div class="contact">
      <p class="contact-phone">PH +64 21 574 613</p>
      <p class="contact-email">r.thornbury@vestaadvisory.co.nz</p>
    </div>
    <div class="silver-band silver-band--contact"></div>
    <div class="silver-band silver-band--bottom"></div>
  </section>

  <section class="card card--back" aria-label="Business card back">
    <div class="brand">
      <div class="brand-dot"></div>
      <div class="brand-name">Vesta Advisory LTD</div>
    </div>
  </section>
</main>
</body>
</html>
```